Letter and Envelope Design For Harborline Realty

Please design a letter and an envelope incorporating our logo (See Attached). We are also launched a business card contest. Since we want them to match, please feel free to submit a design for both the business card and also the letter design and envelope.

Requirements
Must have
• The envelope, the letter and the business cards must match somehow connecting the designs. We want them to have something that holds them together besides the logo.

```html
<!DOCTYPE html>
<html lang="en">
<head>
<meta charset="utf-8">
<title>Harborline Realty Stationery</title>
<link href="https://fonts.googleapis.com/css2?family=Josefin+Sans:wght@300;400&family=Roboto:wght@400&display=swap" rel="stylesheet">
<style>
:root{
  --bg:#dedede;
  --paper:#f7f7f7;
  --navy:#001a8c;
  --grey:#5a5a5a;
  --ink:#4a4a4a;
  --white:#ffffff;
}
*{margin:0;padding:0;box-sizing:border-box}
html,body{width:1200px;height:877px;overflow:hidden;background:var(--bg)}
body{position:relative;font-family:"Josefin Sans",sans-serif;color:var(--ink)}
.sheet{position:absolute;background:var(--paper);overflow:hidden}
.letter{left:69px;top:64px;width:527px;height:742px}
.envelope-back{left:614px;top:269px;width:531px;height:241px}
.envelope-front{left:614px;top:563px;width:532px;height:243px}
.wave{position:absolute;left:0;bottom:0;width:100%}

.brand{position:absolute;display:flex;flex-direction:column;align-items:center;text-align:center;font-family:"Josefin Sans",sans-serif;font-weight:400;color:var(--navy)}
.brand-ring{display:block;flex:none;margin-bottom:6px;width:48px;height:48px;border:2.5px solid var(--navy);border-radius:50%}
.brand-name{display:block;font-size:13px;line-height:1.15;letter-spacing:1.6px}
.letter .brand{left:35px;top:40px;width:145px}
.letter .brand .brand-name{font-size:13.5px}

.salutation{position:absolute;left:46px;top:209px;font-size:14px;font-weight:300;color:#555}
.body-copy{position:absolute;left:46px;top:250px;width:438px;font-size:7.7px;line-height:11.4px;font-weight:400;color:#555;text-align:justify}
.body-copy p{margin-bottom:11.4px}
.closing{position:absolute;left:46px;top:488px;font-size:7.7px;font-weight:400;color:#555}
.signature{position:absolute;left:42px;top:520px;width:94px;height:38px;background:linear-gradient(90deg,rgba(0,26,140,.12),rgba(0,26,140,.05));border-radius:4px}

.contact{position:absolute;right:43px;top:688px;text-align:right;font-family:Roboto,sans-serif;font-size:8.3px;line-height:10.6px;color:var(--white)}
.contact li{list-style:none;display:flex;justify-content:flex-end;align-items:center;gap:5px}
.contact svg{width:7px;height:7px;fill:var(--white)}
.contact .address{margin-top:2px}

.flap{position:absolute;left:0;top:0;width:531px;height:74px}
.flap-name{position:absolute;left:0;top:31px;width:531px;text-align:center;font-size:11px;letter-spacing:2px;color:var(--white)}

.envelope-front .brand{left:10px;top:24px;width:140px}
.envelope-front .brand-ring{width:38px;height:38px;margin-bottom:5px}
.envelope-front .brand-name{font-size:11px;line-height:12px}
.return-address{display:block;margin-top:6px;font-family:Roboto,sans-serif;font-size:7.8px;line-height:9.8px;letter-spacing:0;color:#444}
.web{position:absolute;right:27px;top:213px;font-family:Roboto,sans-serif;font-size:7.6px;letter-spacing:2.2px;color:var(--white)}
</style>
</head>
<body>

<section class="sheet letter">
  <div class="brand"><span class="brand-ring"></span><span class="brand-name">HARBORLINE<br>REALTY</span></div>
  <p class="salutation">Dear Mr. Carter,</p>
  <div class="body-copy">
    <p>Lorem ipsum dolor sit amet, consectetur adipiscing elit. Donec orci purus, luctus vitae dignissim eu, iaculis sed purus. Vivamus faucibus, ipsum nec aliquet viverra, leo mauris condimentum ligula, sit amet sagittis enim ligula quis arcu. Nam egestas tortor id nisi porttitor mattis. In tortor ante, ultricies in suscipit a, tempus non massa. Vivamus et auctor mi. Fusce vel massa nulla. Phasellus nec eros mauris, et scelerisque orci.</p>
    <p>Donec malesuada orci vitae nulla accumsan porta a id massa. Quisque accumsan iaculis magna sit amet fringilla. Maecenas consequat, magna eget tincidunt semper, odio nibh rutrum mi, id feugiat ante nisi eu risus. Vestibulum nunc orci, rhoncus a placerat in, ultricies in mi. Cras mattis varius eros, vel fringilla nisi suscipit eget. Quisque scelerisque sagittis nulla at porttitor.</p>
    <p>Sed id augue vitae urna euismod commodo aliquet a quam. Pellentesque arcu velit, cursus et malesuada ut, consequat et diam. Nullam erat sem, rhoncus id ullamcorper vitae, rhoncus et arcu. In ultricies ultricies nulla, ut rutrum nisi iaculis at. Donec eu magna a metus ornare faucibus. Fusce aliquet faucibus ultricies. Morbi semper, est id tincidunt gravida, sem arcu adipiscing lacus, ac bibendum nulla leo eu purus. Quisque nec diam sed risus consectetur a ccumsan quis quis nibh. Vestibulum id purus lorem.</p>
    <p>It is a long established fact that a reader will be distracted by the readable content of a page when looking at its layout. The point of using Lorem Ipsum is that it has a more-or-less normal distribution of letters, as opposed to using 'Content here, content here', making it look like readable English. Many desktop publishing packages</p>
  </div>
  <p class="closing">Sincerely,</p>
  <div class="signature" role="img" aria-label="Handwritten signature of the sender"></div>

  <svg class="wave" viewBox="0 0 527 90" height="90" aria-hidden="true">
    <path fill="var(--navy)" d="M0,56 C40,73 90,83 140,81 C260,76 380,28 470,24 C500,24 518,32 527,40 L527,90 L0,90Z"/>
    <path fill="var(--grey)" d="M110,83 C240,78 360,16 460,11 C495,10 516,24 527,34 L527,28 C514,12 495,4 460,5 C360,9 240,70 110,83Z"/>
  </svg>
  <ul class="contact">
    <li>555 014 2290 <svg viewBox="0 0 10 10"><path d="M2 0l2 2-1 2c1 1 2 2 3 3l2-1 2 2-2 2C4 10 0 6 0 2z"/></svg></li>
    <li>hello@harborline.com <svg viewBox="0 0 10 10"><path d="M0 2h10v6H0zM0 2l5 4 5-4"/></svg></li>
    <li>www.harborline.com <svg viewBox="0 0 10 10"><circle cx="5" cy="5" r="5"/></svg></li>
    <li class="address">214 Quayside Drive, Anchorage, Alaska 99501</li>
  </ul>
</section>

<section class="sheet envelope-back">
  <svg class="flap" viewBox="0 0 531 74" aria-hidden="true">
    <path fill="var(--navy)" d="M0,0 L531,0 L522,40 Q515,74 485,74 L46,74 Q16,74 9,40 Z"/>
  </svg>
  <p class="flap-name">HARBORLINE REALTY</p>
</section>

<section class="sheet envelope-front">
  <div class="brand">
    <span class="brand-ring"></span>
    <span class="brand-name">HARBORLINE<br>REALTY</span>
    <span class="return-address">214 Quayside Drive<br>Anchorage, Alaska 99501</span>
  </div>
  <svg class="wave" viewBox="0 0 532 80" height="80" aria-hidden="true">
    <path fill="var(--navy)" d="M0,50 C40,64 80,72 120,72 C240,70 360,18 450,14 C490,12 518,26 532,36 L532,80 L0,80Z"/>
    <path fill="var(--grey)" d="M100,73 C230,68 350,10 440,6 C485,4 515,18 532,32 L532,27 C514,10 485,0 440,1 C350,4 230,62 100,73Z"/>
  </svg>
  <p class="web">www.harborlinerealty.com</p>
</section>

</body>
</html>
```